QP Fiduciary Website Redesign Contest

We want to refresh our website to be more insitutional, professional for an international audience. We have designed a new logo for this purpose and that has been attached. A full brand brief and positioning statement has also been attached. Please read through all the documents carefully before designing. The old website is found here: https://qp-fiduciary.example/

Target Market(s)

Actuaries and associated businesses internationally

Industry/Entity Type

professional services - actuaries

Number of Pages Required

3 page

Font styles to use
Sans Serif

Colors
0054AA
0677BA
7BADD7
CADEEF
E8F1F8
0094D4
00A9DD
6FCCEA
C7EBF8
E9F6FB
F0912C
F2A743
F7CA91
FBE8D2
FDF5EE
EE7325
F08F49
F5BC92
FAE3D3
FDF4ED
EB3D1F
EC4F4E
F09395
F8D3D4
FCEDEE

Requirements
Must have
• blues and greens to match the logo color, complimentary colors, navigation
Nice to have
• old site: https://qp-fiduciary.example/

```html
<!DOCTYPE html>
<html lang="en">
<head>
<meta charset="utf-8">
<title>QP Fiduciary — Actuarial Software</title>
<link href="https://fonts.googleapis.com/css2?family=Lato:ital,wght@0,400;0,700;0,900;1,700;1,900&display=swap" rel="stylesheet">
<style>
:root{
  --navy:#0a2557;
  --navy-deep:#061a40;
  --blue:#0054AA;
  --blue-mid:#0677BA;
  --sky:#0094D4;
  --mist:#E8F1F8;
  --mist-2:#eef4fa;
  --orange:#EE7325;
  --ink:#1a1f2e;
  --grey:#5b6475;
  --line:#d9e3ee;
  --white:#ffffff;
}
*{box-sizing:border-box;margin:0;padding:0}
html,body{width:1200px;height:4332px;overflow:hidden}
body{font-family:"Lato",Arial,sans-serif;color:var(--ink);background:var(--white);position:relative}
.abs{position:absolute}
.accent{color:var(--orange);font-style:italic;font-weight:900}
.btn{display:inline-block;border-radius:22px;font-size:11px;font-weight:900;letter-spacing:.6px;text-transform:uppercase;padding:11px 22px;white-space:nowrap}
.btn-orange{background:var(--orange);color:var(--white)}
.btn-blue{background:var(--blue);color:var(--white)}
.btn-white{background:var(--white);color:var(--navy)}
.btn-outline{border:1px solid #b9c3cf;color:var(--ink);border-radius:16px;padding:7px 14px;font-size:10px}
.section-title{position:absolute;left:0;width:1200px;text-align:center;font-size:40px;font-weight:900;color:var(--ink)}
.section-sub{position:absolute;left:0;width:1200px;text-align:center;font-size:13px;color:var(--grey)}

/* hero */
.hero{left:0;top:0;width:1200px;height:520px;background:linear-gradient(100deg,var(--navy-deep),var(--navy) 55%,#0d3a7a);overflow:hidden}
.hero-photo{left:600px;top:0;width:640px;height:460px;background:linear-gradient(135deg,#8fa9c6,#c9d6e2 40%,#6c86a6);border-radius:0 0 0 260px}
.nav{left:0;top:0;width:1200px;height:72px}
.brand{left:80px;top:22px;display:flex;align-items:center;gap:10px;color:var(--white);font-size:22px;font-weight:900}
.brand-dot{width:22px;height:22px;border-radius:50%;background:var(--orange)}
.nav-links{left:370px;top:30px;display:flex;gap:18px;color:var(--white);font-size:10px;font-weight:700;letter-spacing:.5px}
.nav-cta{left:740px;top:19px;display:flex;gap:12px}
.nav-cta .btn{padding:10px 18px;font-size:10px}
.hero-title{left:80px;top:100px;width:500px;font-size:46px;line-height:1.13;font-weight:900;color:var(--white)}
.hero-text{left:80px;top:300px;width:470px;font-size:14px;line-height:1.5;color:#d7e2f1}
.hero-btn{left:80px;top:370px}

/* pillars */
.pillars{left:165px;top:775px;width:870px;display:flex;gap:20px}
.pillar{flex:1;background:var(--mist);border-radius:10px;padding:22px 18px;height:190px}
.pillar-icon{width:44px;height:44px;border-radius:10px;background:var(--white);display:flex;align-items:center;justify-content:center;margin-bottom:12px}
.pillar h3{font-size:15px;font-weight:900;margin-bottom:8px;color:var(--ink)}
.pillar p{font-size:11px;line-height:1.5;color:var(--grey)}

/* core solutions */
.band{left:0;width:1200px}
.solutions-head{left:190px;top:1270px;width:400px}
.solutions-head h2{font-size:40px;font-weight:900}
.solutions-head p{font-size:12px;color:var(--grey);margin-top:8px}
.sol-cell{padding:0 40px;text-align:center}
.sol-cell h3{font-size:16px;font-weight:900;margin:10px 0 8px}
.sol-cell p{font-size:13px;line-height:1.5;color:var(--grey)}
.sol-cell .more{display:block;margin-top:10px;font-size:10px;font-weight:900;letter-spacing:.5px}
.sol-icon{width:44px;height:44px;margin:0 auto;display:block}
.sol-hub{left:570px;top:1390px;width:60px;height:60px;border-radius:50%;background:var(--white);border:2px solid var(--line);display:flex;align-items:center;justify-content:center;font-size:15px;font-weight:900;color:var(--blue)}

/* characteristics */
.char-photo{left:160px;top:2100px;width:460px;height:340px;border-radius:18px;background:linear-gradient(140deg,#7e93ad,#c8d2dc 50%,#5b7190)}
.char-item{background:var(--white);border-radius:10px;box-shadow:0 6px 20px rgba(10,37,87,.12);display:flex;align-items:center;gap:12px;padding:14px 16px;font-size:13px;font-weight:700}
.char-icon{width:32px;height:32px;border-radius:8px;background:var(--mist);display:flex;align-items:center;justify-content:center;flex:none}

/* insights */
.post{width:280px}
.post-img{height:250px;border-radius:14px}
.post-meta{display:flex;gap:14px;font-size:10px;color:var(--grey);margin:16px 0 10px}
.post h3{font-size:17px;font-weight:900;line-height:1.25;margin-bottom:8px}
.post p{font-size:11px;line-height:1.5;color:var(--grey);margin-bottom:14px}

/* cta */
.cta{left:165px;top:3610px;width:870px;height:290px;border-radius:30px;background:linear-gradient(120deg,var(--blue),var(--blue-mid) 60%,var(--sky));text-align:center;color:var(--white);padding-top:48px}
.cta h2{font-size:40px;font-weight:900;line-height:1.12}
.cta h2 em{font-style:italic}
.cta p{font-size:13px;line-height:1.5;color:#dbe9f7;width:460px;margin:16px auto 22px}

/* footer */
.footer{left:0;top:3950px;width:1200px;height:382px;background:var(--navy-deep);color:var(--white)}
.footer h4{font-size:15px;font-weight:900;margin-bottom:14px}
.footer li{list-style:none;font-size:12px;color:#c6d2e4;margin-bottom:8px}
.contact-row{display:flex;gap:8px;font-size:11px;color:#c6d2e4;line-height:1.45;margin-bottom:10px}
.social-row{display:flex;align-items:center;gap:10px;font-size:12px;color:#c6d2e4;margin-bottom:10px}
.social-dot{width:22px;height:22px;border-radius:50%;background:var(--blue-mid)}
.social-row.active .social-dot{background:var(--orange)}
.newsletter{display:flex;align-items:center;width:240px;height:38px;border-radius:20px;background:var(--white);padding:0 4px 0 16px;font-size:11px;color:#8a93a3;justify-content:space-between}
.newsletter span.go{width:30px;height:30px;border-radius:50%;background:var(--orange)}
.footer-bottom{left:160px;top:330px;width:880px;border-top:1px solid #22386a;padding-top:14px;display:flex;justify-content:space-between;font-size:11px;color:#9fb0c8}
</style>
</head>
<body>

<!-- HERO -->
<header class="hero abs">
  <div class="hero-photo abs" role="img" aria-label="Photo of a team of analysts reviewing charts in a meeting room"></div>
  <svg class="abs" style="left:0;top:420px" width="1200" height="100" viewBox="0 0 1200 100">
    <path d="M0 60 C300 10 700 0 1200 30 L1200 100 L0 100Z" fill="var(--orange)"/>
    <path d="M0 75 C320 30 720 20 1200 48 L1200 100 L0 100Z" fill="var(--blue)"/>
    <path d="M0 88 C340 55 760 45 1200 70 L1200 100 L0 100Z" fill="var(--white)"/>
  </svg>
  <nav class="nav abs">
    <div class="brand abs"><span class="brand-dot"></span>QP Fiduciary</div>
    <div class="nav-links abs"><span>PLATFORM</span><span>SOLUTIONS</span><span>INSIGHTS</span><span>COMPANY</span><span>CONTACT</span></div>
    <div class="nav-cta abs"><span class="btn btn-blue">Request a technical walkthrough</span><span class="btn btn-white">Client login</span></div>
  </nav>
  <h1 class="hero-title abs">Actuarial Software For Structured, <span class="accent">Auditable Financial</span> Analysis.</h1>
  <p class="hero-text abs">QP Fiduciary Develops Software That Translates Established Actuarial Methodologies Into Disciplined, Decision-Ready Tools</p>
  <span class="hero-btn btn btn-orange abs">Request a technical walkthrough</span>
</header>

<!-- PILLARS -->
<h2 class="section-title" style="top:640px">One Platform, <span class="accent">Four Pillars</span></h2>
<p class="section-sub" style="top:700px">Purpose-Built To Bring Clarity, Control, And Compliance To Actuarial Work</p>
<div class="pillars abs">
  <div class="pillar"><div class="pillar-icon"><svg width="24" height="24" viewBox="0 0 24 24"><rect x="3" y="4" width="18" height="4" rx="1" fill="var(--blue)"/><rect x="3" y="10" width="12" height="4" rx="1" fill="var(--sky)"/><rect x="3" y="16" width="15" height="4" rx="1" fill="var(--orange)"/></svg></div><h3>Structured Workflows</h3><p>Standardised processes that reduce errors and enforce consistency across teams and regions.</p></div>
  <div class="pillar"><div class="pillar-icon"><svg width="24" height="24" viewBox="0 0 24 24"><circle cx="12" cy="12" r="8" fill="none" stroke="var(--blue)" stroke-width="2"/><circle cx="12" cy="12" r="3" fill="var(--orange)"/></svg></div><h3>Transparency Of Assumptions</h3><p>Every input, parameter and override is visible, documented and version controlled.</p></div>
  <div class="pillar"><div class="pillar-icon"><svg width="24" height="24" viewBox="0 0 24 24"><path d="M5 12l4 4 10-10" fill="none" stroke="var(--blue)" stroke-width="2.5"/></svg></div><h3>Auditability</h3><p>End-to-end traceability with full audit trails designed for internal and regulatory reviews.</p></div>
  <div class="pillar"><div class="pillar-icon"><svg width="24" height="24" viewBox="0 0 24 24"><path d="M12 3l8 3v6c0 5-4 8-8 9-4-1-8-4-8-9V6z" fill="none" stroke="var(--blue)" stroke-width="2"/></svg></div><h3>Governance</h3><p>Built-in controls, role-based access and approval flows to meet global compliance.</p></div>
</div>

<!-- CORE SOLUTIONS -->
<svg class="band abs" style="top:1150px" width="1200" height="660" viewBox="0 0 1200 660">
  <path d="M0 60 C400 0 800 0 1200 50 L1200 600 C800 660 400 660 0 610Z" fill="var(--mist-2)"/>
</svg>
<div class="abs" style="left:600px;top:1210px;width:450px;height:220px;border-radius:60px 60px 0 0;background:var(--white)"></div>
<div class="abs" style="left:150px;top:1420px;width:900px;height:230px;border-radius:0 0 60px 60px;background:var(--white)"></div>
<div class="abs" style="left:150px;top:1420px;width:900px;height:1px;background:var(--line)"></div>
<div class="abs" style="left:600px;top:1230px;width:1px;height:400px;background:var(--line)"></div>
<div class="solutions-head abs"><h2>Core <span class="accent">Solutions</span></h2><p>Modular Applications That Integrate Seamlessly — Or Work Standalone</p></div>
<div class="sol-cell abs" style="left:610px;top:1240px;width:430px">
  <svg class="sol-icon" viewBox="0 0 44 44"><rect x="8" y="24" width="6" height="12" fill="var(--blue)"/><rect x="19" y="16" width="6" height="20" fill="var(--sky)"/><rect x="30" y="8" width="6" height="28" fill="var(--orange)"/></svg>
  <h3>Reserving &amp; Valuation</h3><p>Lorem ipsum is simply dummy text of the printing and typesetting industry. Lorem ipsum has been the industry's standard dummy text ever since</p><span class="more">READ MORE</span></div>
<div class="sol-cell abs" style="left:160px;top:1460px;width:430px">
  <svg class="sol-icon" viewBox="0 0 44 44"><circle cx="22" cy="22" r="14" fill="none" stroke="var(--blue)" stroke-width="3"/><path d="M22 12v20M17 17h8a3 3 0 010 6h-6a3 3 0 000 6h9" fill="none" stroke="var(--orange)" stroke-width="2.5"/></svg>
  <h3>Pricing</h3><p>Lorem ipsum is simply dummy text of the printing and typesetting industry. Lorem ipsum has been the industry's standard dummy text ever since</p><span class="more">READ MORE</span></div>
<div class="sol-cell abs" style="left:610px;top:1460px;width:430px">
  <svg class="sol-icon" viewBox="0 0 44 44"><path d="M22 6l14 5v10c0 9-6 14-14 17C14 35 8 30 8 21V11z" fill="none" stroke="var(--blue)" stroke-width="3"/><path d="M16 22l4 4 8-8" fill="none" stroke="var(--orange)" stroke-width="3"/></svg>
  <h3>Enterprise Risk Management</h3><p>Lorem ipsum is simply dummy text of the printing and typesetting industry. Lorem ipsum has been the industry's standard dummy text ever since</p><span class="more">READ MORE</span></div>
<div class="sol-hub abs">QP</div>

<!-- CHARACTERISTICS -->
<h2 class="section-title" style="top:1900px">Key Platform <span class="accent">Characteristics</span></h2>
<svg class="abs" style="left:130px;top:2070px" width="520" height="400" viewBox="0 0 520 400"><path d="M20 380 C10 200 60 40 200 10" fill="none" stroke="var(--orange)" stroke-width="6"/></svg>
<div class="char-photo abs" role="img" aria-label="Photo of colleagues working together at a laptop"></div>
<div class="char-item abs" style="left:700px;top:2140px;width:230px"><span class="char-icon"><svg width="18" height="18" viewBox="0 0 18 18"><rect x="2" y="3" width="14" height="3" fill="var(--blue)"/><rect x="2" y="8" width="9" height="3" fill="var(--sky)"/><rect x="2" y="13" width="12" height="3" fill="var(--orange)"/></svg></span>Structured Workflows</div>
<div class="char-item abs" style="left:950px;top:2220px;width:240px"><span class="char-icon"><svg width="18" height="18" viewBox="0 0 18 18"><circle cx="9" cy="9" r="7" fill="none" stroke="var(--blue)" stroke-width="2"/><path d="M2 9h14M9 2c3 3 3 11 0 14M9 2c-3 3-3 11 0 14" fill="none" stroke="var(--blue)" stroke-width="1.2"/></svg></span>Multi-Jurisdictional Review Support</div>
<div class="char-item abs" style="left:700px;top:2300px;width:230px"><span class="char-icon"><svg width="18" height="18" viewBox="0 0 18 18"><circle cx="9" cy="9" r="6" fill="none" stroke="var(--blue)" stroke-width="2"/><circle cx="9" cy="9" r="2" fill="var(--orange)"/></svg></span>Transparent Assumptions</div>
<div class="char-item abs" style="left:950px;top:2380px;width:240px"><span class="char-icon"><svg width="18" height="18" viewBox="0 0 18 18"><rect x="3" y="9" width="3" height="6" fill="var(--blue)"/><rect x="8" y="5" width="3" height="10" fill="var(--sky)"/><rect x="13" y="2" width="3" height="13" fill="var(--orange)"/></svg></span>comparative analysis capability</div>

<!-- INSIGHTS -->
<svg class="band abs" style="top:2480px" width="1200" height="960" viewBox="0 0 1200 960">
  <path d="M0 70 C400 0 800 0 1200 60 L1200 910 C800 960 400 960 0 900Z" fill="var(--mist-2)"/>
</svg>
<h2 class="section-title" style="top:2585px">Insights &amp; Thought <span class="accent">Leadership</span></h2>
<p class="section-sub" style="top:2645px">Perspectives From Our Actuaries And Engineers</p>
<article class="post abs" style="left:160px;top:2705px">
  <div class="post-img" style="background:linear-gradient(140deg,#6f7f93,#b9c4cf 55%,#4f5f75)" role="img" aria-label="Photo of a professional reviewing data on a laptop"></div>
  <div class="post-meta"><span>Jan 12, 2026</span><span>AUTHOR: Anna Reed</span></div>
  <h3>Evolution into Technology-Led Actuarial Platform</h3>
  <p>From humble beginnings our firm has grown into a trusted provider of structured actuarial technology for global clients.</p>
  <span class="btn btn-outline">Read more</span>
</article>
<article class="post abs" style="left:460px;top:2705px">
  <div class="post-img" style="background:linear-gradient(150deg,#8cc9a0,#3e9a78 60%,#2d6f86)" role="img" aria-label="Illustration promoting financial literacy and inclusion"></div>
  <div class="post-meta"><span>Jan 05, 2026</span><span>AUTHOR: Mark Ellis</span></div>
  <h3>Financial Literacy and Inclusion: Leveraging actuarial expertise to improve financial understanding and decision-making</h3>
  <span class="btn btn-outline">Read more</span>
</article>
<article class="post abs" style="left:760px;top:2705px">
  <div class="post-img" style="background:linear-gradient(140deg,#1f3a6a,#3a6fa8 55%,#c89a4a)" role="img" aria-label="Photo of business people in a meeting with a glowing lightbulb graphic"></div>
  <div class="post-meta"><span>Dec 28, 2025</span><span>AUTHOR: Priya Shah</span></div>
  <h3>RBC (Risk-Based Capital)</h3>
  <p>Risk-based capital is a regulatory framework ensuring insurers hold capital in proportion to the risks they carry on their books.</p>
  <span class="btn btn-outline">Read more</span>
</article>

<!-- CTA -->
<section class="cta abs">
  <h2>Ready To See<br><em>QP Fiduciary In Action?</em></h2>
  <p>Schedule A Personalised Technical Walkthrough And Discover How Our Platform Can Transform Your Actuarial Processes.</p>
  <span class="btn btn-orange">Request a technical walkthrough</span>
</section>

<!-- FOOTER -->
<footer class="footer abs">
  <svg class="abs" style="left:0;top:-40px" width="1200" height="80" viewBox="0 0 1200 80"><path d="M0 40 C400 0 800 0 1200 40 L1200 80 L0 80Z" fill="var(--navy-deep)"/><path d="M0 40 C400 0 800 0 1200 40" fill="none" stroke="var(--orange)" stroke-width="3"/></svg>
  <div class="abs" style="left:160px;top:50px;width:280px">
    <div style="display:flex;align-items:center;gap:10px;font-size:22px;font-weight:900;margin-bottom:16px"><span class="brand-dot"></span>QP Fiduciary</div>
    <p style="font-size:11px;line-height:1.5;color:#c6d2e4;margin-bottom:18px">Latest Industry Updates, Product News And Expert Insights. Subscribe To Our Newsletter.</p>
    <div class="newsletter">Your email<span class="go"></span></div>
  </div>
  <div class="abs" style="left:500px;top:50px">
    <h4>Quick Links</h4>
    <ul><li>Home</li><li>Platform</li><li>Solutions</li><li>Insights</li><li>Company</li><li>Contact</li></ul>
  </div>
  <div class="abs" style="left:690px;top:50px;width:220px">
    <h4>Contact Details</h4>
    <div class="contact-row"><svg width="12" height="14" viewBox="0 0 12 14"><path d="M6 1a4.5 4.5 0 014.5 4.5C10.5 9 6 13 6 13S1.5 9 1.5 5.5A4.5 4.5 0 016 1z" fill="var(--orange)"/></svg><span>48 Harbor Row, Suite 200,<br>Easton, MA 02356</span></div>
    <div class="contact-row"><svg width="12" height="12" viewBox="0 0 12 12"><path d="M2 1l3 1 0 3-1.5 1a7 7 0 003 3L8 7.5l3 0 0 3c-5 1-10-4-9-9.5z" fill="var(--orange)"/></svg><span>Phone<br>+1 (555) 014-2290</span></div>
    <div class="contact-row"><svg width="12" height="10" viewBox="0 0 12 10"><rect x="0.5" y="0.5" width="11" height="9" rx="1" fill="none" stroke="var(--orange)"/><path d="M1 1l5 4 5-4" fill="none" stroke="var(--orange)"/></svg><span>hello@qp-fiduciary.example</span></div>
  </div>
  <div class="abs" style="left:950px;top:50px">
    <h4>Social Media</h4>
    <div class="social-row active"><span class="social-dot"></span>Community</div>
    <div class="social-row"><span class="social-dot"></span>Video</div>
    <div class="social-row"><span class="social-dot"></span>Network</div>
    <div class="social-row"><span class="social-dot"></span>Gallery</div>
  </div>
  <div class="footer-bottom abs"><span>© 2026 QP Fiduciary. All Rights Reserved.</span><span>Privacy · Terms</span></div>
</footer>

</body>
</html>
```